9x12 Business Brochure, 3 fold, for Internet Marketing Company

I'd like to have a brochure designed for my Internet marketing company. I have the content all ready, 10 Internet Marketing Myths, which you can see here: http://www.brisklanternstudio.example/usual-web-promotion-fables/. I'm looking for something creative and business to business. The company is all about Internet marketing. I like the "http://" header I use at our website. People like it too and identify with it. Audience is business owners 35 to 55 years old. I use blue at my website. I *think* I would like the cover page (front page) to open with some attention grabbing text, that basically takes most of the front page of the brochure. It would probably say: "I Can Help You Get BETTER RESULTS from Your Website, More Traffic, TOP RANKINGS at Quorble, More Leads and MORE SALES. But first you'll have to avoid these common Internet marketing myths..." The inside pages would have the content from above (the 10 myths). The back page would have testimonials that I can provide. And the inside folded in page (or what I call the inside folded in page) would have a list of services. I think I want the dimensions 12x9 which is a larger sized, three-fold brochure.

Target Market(s)

I use this brochure to send to business owners and managers to show them I know what I'm talking about and and expert. See attachment for content.

Industry/Entity Type

Marketing

Requirements
Should not have
• No clipart. Probably not illustrations. Photos. The "http://" used at the site is something people "connect" with and get that this is about Internet marketing.

```html
<!DOCTYPE html>
<html lang="en">
<head>
<meta charset="utf-8">
<title>Practical Online Marketing – Tri-fold Brochure</title>
<link rel="stylesheet" href="https://fonts.googleapis.com/css2?family=Arimo:ital,wght@0,400;0,700;1,400&display=swap">
<style>
  :root {
    --navy-deep: #0a1340;
    --navy-mid: #1b3a78;
    --navy-glow: #2d5aa0;
    --ink: #111111;
    --body-grey: #6a6a6a;
    --story-blue: #1f4f8a;
    --sky: #5cc6e6;
    --ice: #bfe7f5;
    --white: #ffffff;
    --black: #000000;
    --page: #ffffff;
  }
  * { margin: 0; padding: 0; box-sizing: border-box; }
  html, body { width: 1200px; height: 901px; overflow: hidden; background: var(--page); }
  body { font-family: "Arimo", Arial, sans-serif; }

  .brochure { position: relative; width: 1200px; height: 901px; display: flex; }
  .panel { position: relative; width: 400px; height: 901px; overflow: hidden; }

  /* Services panel */
  .panel--services {
    background: radial-gradient(ellipse 75% 45% at 60% 45%, var(--navy-glow) 0%, var(--navy-mid) 35%, var(--navy-deep) 80%);
    color: var(--white);
  }
  .services__title {
    position: absolute; left: 42px; top: 38px;
    font-size: 43px; font-weight: 700; line-height: 46px;
  }
  .services__list {
    position: absolute; left: 28px; top: 148px; list-style: none;
  }
  .services__list li {
    position: relative; padding-left: 20px;
    font-size: 17.5px; line-height: 30.6px;
  }
  .services__list li::before {
    content: ""; position: absolute; left: 0; top: 11px;
    width: 9px; height: 9px; background: #d8dde8;
  }
  .services__quote {
    position: absolute; left: 48px; top: 723px; width: 340px;
    font-size: 18.5px; font-style: italic; line-height: 31px;
  }
  .services__call {
    position: absolute; left: 42px; top: 839px;
    font-size: 25px; font-weight: 700;
  }

  /* Stories panel */
  .panel--stories { background: var(--white); }
  .stories__art {
    position: absolute; left: 20px; top: 0; width: 352px; height: 178px;
    background: linear-gradient(90deg, #1a6a9a 0%, #5fb6d6 45%, #dfeef6 75%, #f4f8fb 100%);
    border-radius: 4px;
  }
  .stories__title {
    position: absolute; left: 22px; top: 182px;
    font-size: 42px; font-weight: 700; color: var(--ink);
  }
  .stories__body { position: absolute; left: 29px; top: 238px; width: 343px; }
  .story {
    font-size: 13.2px; line-height: 19.6px; color: var(--body-grey);
    text-align: justify; margin-bottom: 18px;
  }
  .story__label { font-size: 17px; font-weight: 700; color: var(--story-blue); }
  .stories__sign {
    position: absolute; left: 0; width: 400px; top: 828px;
    text-align: center; font-size: 18px; font-weight: 700; line-height: 22px; color: var(--ink);
  }

  /* Front panel */
  .panel--front { background: var(--black); color: var(--white); }
  .front__hero {
    position: absolute; left: 0; top: 0; width: 400px; height: 318px;
    background: radial-gradient(ellipse 80% 70% at 50% 45%, #1d4f78 0%, #0d2a48 50%, #03101e 100%);
  }
  .front__brand {
    position: absolute; left: 0; width: 400px; top: 36px;
    text-align: center; color: var(--ice); font-weight: 700;
    text-shadow: 0 0 10px rgba(120, 210, 240, .55);
  }
  .front__brand-top { display: block; font-size: 54px; line-height: 58px; letter-spacing: 1px; }
  .front__brand-mid { display: block; font-size: 104px; line-height: 96px; letter-spacing: -1px; }
  .front__brand-low { display: block; font-size: 60px; line-height: 66px; }
  .front__band {
    position: absolute; left: 0; top: 318px; width: 400px; height: 100px;
    background: linear-gradient(180deg, #2d7fc4 0%, #9fd0ef 45%, #e9f4fb 70%, #3b86c4 100%);
  }
  .front__pitch {
    position: absolute; left: 0; width: 400px; top: 482px;
    text-align: center; font-weight: 700;
  }
  .pitch--sky { color: var(--sky); font-size: 25px; line-height: 30px; display: block; }
  .pitch--big { color: var(--white); font-size: 33px; line-height: 34px; display: block; }
  .pitch-row { display: block; line-height: 34px; }
  .pitch-row .pitch--big, .pitch-row .pitch--sky { display: inline; }
  .front__myths {
    position: absolute; left: 0; width: 400px; top: 825px; top: 822px;
    text-align: center; font-size: 20px; line-height: 23px;
  }
  .front__myths { top: 823px; }
  .front__lead { position: absolute; left: 0; width: 400px; top: 824px; }
  .front__teaser {
    position: absolute; left: 0; width: 400px; top: 823px;
  }
  .front__intro {
    position: absolute; left: 0; width: 400px; top: 823px;
  }
  .front__note {
    position: absolute; left: 0; width: 400px; top: 823px;
  }
  .front__contact {
    position: absolute; left: 0; width: 400px; top: 822px;
  }
</style>
</head>
<body>
<main class="brochure">

  <section class="panel panel--services">
    <h2 class="services__title">Services &amp;<br>&nbsp;Expertise</h2>
    <ul class="services__list">
      <li>Internet Strategy Development</li>
      <li>Custom Website Design</li>
      <li>Blog Design &amp; Support</li>
      <li>Online Marketing Copywriting</li>
      <li>Social Media Marketing</li>
      <li>Search Engine Optimization (SEO)</li>
      <li>Conversion Optimization</li>
      <li>Content Marketing Management</li>
      <li>Using Friendlink for Business</li>
      <li>Quorble+, Clipstream, Pinboardly</li>
      <li>Email Marketing &amp; Production</li>
      <li>Inquiry and Lead Development</li>
      <li>Quorble AdBoost Pay-Per-Click</li>
      <li>Quorble Local Places (maps)</li>
      <li>E-Commerce Development</li>
      <li>High-Performance Hosting</li>
      <li>Security &amp; Contingency Planning</li>
      <li>One-on-One or Group Training</li>
    </ul>
    <p class="services__quote">“If you think it’s expensive to hire an expert,&nbsp; wait until you hire an amateur.”</p>
    <p class="services__call">Call Us: (800) 555-0143</p>
  </section>

  <section class="panel panel--stories">
    <div class="stories__art" role="img" aria-label="Globe with a curved arrow beside a browser address bar and pointing hand cursor"></div>
    <h2 class="stories__title">Success Stories</h2>
    <div class="stories__body">
      <p class="story"><span class="story__label">Quorble Rankings</span> – “… we have spent over a year trying to get onto page one at Quorble. It has been very frustrating and we’ve wasted a lot of time and money. Dana explained everything very clearly and we did everything he told us. 90 days later we’re now showing up on the first page of Quorble!</p>
      <p class="story"><span class="story__label">Website Design</span> – “We needed a new website that properly reflected our company and the products and services we sell. We started getting more leads within 72 hours of launching the new site Dana and his team designed for us. We’re also getting better results from our Quorble AdBoost pay-per-click advertising and more of those clicks are turning into inquiries!”</p>
      <p class="story"><span class="story__label">More to Come</span> - Lorem ipsum dolor sit amet, consectetur adipiscing elit. Suspendisse justo velit, auctor ut pulvinar a, egestas non urna. Suspendisse potenti. Sed at pellentesque dolor. Vivamus sed nibh nisl. Nunc tortor tellus, facilisis eget pretium vitae, porttitor quis libero.</p>
      <p class="story"><span class="story__label">More to Come</span> - Lorem ipsum dolor sit amet, consectetur adipiscing elit. Suspendisse justo velit, auctor ut pulvinar a, egestas non urna. Suspendisse potenti. Sed at pellentesque dolor. Vivamus sed nibh nisl. Nunc tortor tellus, facilisis eget pretium vitae, porttitor quis libero.</p>
    </div>
    <p class="stories__sign">DANA WHITLOW<br>Dana Whitlow Consulting (.com)</p>
  </section>

  <section class="panel panel--front">
    <div class="front__hero" role="img" aria-label="Dark blue world map overlaid with glowing digital code"></div>
    <h1 class="front__brand">
      <span class="front__brand-top">PRACTICAL</span>
      <span class="front__brand-mid">Online</span>
      <span class="front__brand-low">Marketing</span>
    </h1>
    <div class="front__band" role="img" aria-label="Close-up of a browser address bar reading http://www with an arrow cursor"></div>
    <p class="front__pitch">
      <span class="pitch--sky">I Can Help You Get</span>
      <span class="pitch--big">BETTER RESULTS</span>
      <span class="pitch--sky">from Your Website,</span>
      <span class="pitch--sky">More Traffic,</span>
      <span class="pitch-row"><span class="pitch--big">TOP RANKINGS</span> <span class="pitch--sky">with</span></span>
      <span class="pitch--sky">Quorble, More Inquiries, &amp;</span>
      <span class="pitch--big">MORE SALES</span>
    </p>
    <p style="position:absolute;left:0;width:400px;top:711px;text-align:center;font-size:20px;line-height:23px;">But first you’ll need to avoid these<br>Common Internet Marketing Myths…</p>
    <p style="position:absolute;left:0;width:400px;top:812px;text-align:center;font-size:19px;font-weight:700;line-height:24px;">Dana Whitlow Consulting (.com)</p>
    <p style="position:absolute;left:0;width:400px;top:838px;text-align:center;font-size:27px;font-weight:700;line-height:32px;">(800) 555-0143</p>
  </section>

</main>
</body>
</html>
```